K&R Trailer Rental promo Flyer 5.5x8.5" Flyer

All assets and several pictures of my trailers, that we rent out, are attached.

Flyer dimensions are 5.5"x8.5" - I'll be having it printed on glossy stock.
The dimensions and capacity of the trailers is key.
Include phone number: 555-613-2890 and our website kandrtrailer-example.com

I want something that will really "POP".

Target Market(s)

Blue collar business owners. Recreational offer roads/4x4 folks, used car dealers, contractors/small business owners. Folks with only occasional need for a trailer

Industry/Entity Type

Trailer Rental

Font styles to use
Other font styles liked:
• Designer's choice/no preference

Colors
EE7325
F08F49
F5BC92
FAE3D3
FDF4ED

Requirements
Must have
• Phone number, website, and details about our trailer offerings

```html
<!DOCTYPE html>
<html lang="en">
<head>
<meta charset="utf-8">
<title>K&amp;R Trailer Rental Flyer</title>
<link href="https://fonts.googleapis.com/css2?family=Bebas+Neue&family=Poppins:wght@300;400;600;700;800&display=swap" rel="stylesheet">
<style>
:root{
  --orange:#EE7325;
  --orange-mid:#F08F49;
  --orange-soft:#F5BC92;
  --orange-pale:#FAE3D3;
  --cream:#FDF4ED;
  --ink:#1c1c1c;
  --slate:#4a4a4c;
  --panel:#3a3a3d;
  --panel-edge:#6a6a6c;
  --paper:#ffffff;
  --stage:#e9e6e2;
}
*{margin:0;padding:0;box-sizing:border-box}
html,body{width:1200px;height:879px;overflow:hidden;background:var(--stage)}
.flyer{position:absolute;left:0;top:51px;width:1200px;height:776px;background:var(--paper);font-family:'Poppins',sans-serif;color:var(--slate);overflow:hidden}
.abs{position:absolute}
.bebas{font-family:'Bebas Neue',sans-serif;font-weight:400}
.header-photo{left:0;top:0;width:1200px;height:252px;background:linear-gradient(180deg,var(--orange-pale) 0%,#fbeadd 55%,var(--cream) 100%)}
.logo-art{left:65px;top:16px;width:232px;height:84px;background:linear-gradient(180deg,var(--orange-soft),var(--orange-mid));border-radius:6px}
.brand-name{left:25px;top:106px;font-size:46px;color:var(--ink);letter-spacing:.5px;line-height:1}
.phone{right:28px;top:40px;font-size:66px;line-height:1;color:var(--ink)}
.phone .area{color:var(--orange)}
.city{right:28px;top:102px;font-size:28px;line-height:1;color:var(--orange)}
.site{right:28px;top:130px;font-size:28px;line-height:1;color:var(--ink)}
.headline{left:0;top:170px;width:1200px;text-align:center;font-size:24px;line-height:28px;color:var(--slate)}
.headline strong{color:var(--orange);font-weight:800}
.card{top:262px;height:345px;background:var(--orange)}
.card.left{left:25px;width:376px}
.card.right{left:832px;width:342px}
.card .photo{position:absolute;left:4px;top:4px;right:4px;height:160px;background:linear-gradient(160deg,#cfcac6,#8f8a86 60%,#55514e)}
.card h2{position:absolute;left:10px;top:170px;font-family:'Bebas Neue',sans-serif;font-weight:400;font-size:36px;line-height:1;color:#fff}
.card p{position:absolute;left:13px;right:12px;top:208px;font-size:13px;line-height:16.3px;font-weight:400;color:#fff}
.price{top:619px;height:145px;background:var(--panel);border:4px solid var(--panel-edge);display:flex;color:#fff}
.price.left{left:25px;width:376px}
.price.right{left:832px;width:342px}
.price .col{flex:1;text-align:center;padding-top:8px}
.price .divider{width:0;border-left:2px dashed #fff;margin:16px 0}
.price .title{font-family:'Bebas Neue',sans-serif;font-size:34px;line-height:1}
.price .days{font-size:11px;margin-top:9px}
.price .rate{font-weight:700;font-size:16px;margin-top:18px;line-height:1.2}
.price .rate span{display:block;color:var(--orange-mid)}
.price.right .rate{margin-top:13px;line-height:1.15}
.price.right .rate small{display:block;font-size:13px;color:var(--orange-mid)}
.category{left:454px;top:240px;width:328px;height:80px;border:1.5px dashed var(--orange);background:var(--paper);display:flex;align-items:center;justify-content:center;text-align:center;font-weight:700;font-size:24px;line-height:32px;color:var(--slate)}
.connectors{left:400px;top:230px}
.meet{left:454px;top:326px;width:328px;text-align:center;font-size:58px;line-height:50px;color:var(--slate)}
.meet .hl{color:var(--orange)}
.arrow{top:344px}
.map{left:430px;top:434px;width:374px;height:222px;border:4px solid var(--orange);background:linear-gradient(120deg,#eeeae3 0%,#e4e0da 55%,var(--orange-soft) 82%,var(--orange-mid) 100%)}
.serving{left:430px;top:661px;width:374px;text-align:center;font-size:40px;line-height:1;color:var(--slate)}
.serving span{color:var(--orange)}
.counties{left:430px;top:701px;width:374px;text-align:center;font-size:12px;line-height:15.5px;color:var(--ink)}
.contact{left:430px;top:749px;width:374px;text-align:center;font-size:13px;font-weight:600;color:var(--orange)}
</style>
</head>
<body>
<div class="flyer">
  <div class="abs header-photo" role="img" aria-label="Faded photo of trailers loaded with cars in a driveway"></div>
  <div class="abs logo-art" role="img" aria-label="Illustration of a car on a trailer"></div>
  <div class="abs brand-name bebas">K&amp;R Trailer Rental</div>

  <div class="abs phone bebas"><span class="area">(555)</span>613-2890</div>
  <div class="abs city bebas">Cedar Ridge, MI</div>
  <div class="abs site bebas">WWW.KANDRTRAILER-EXAMPLE.COM</div>

  <div class="abs headline"><strong>WHAT ARE YOU LOOKING FOR?</strong> A trailer to move equipment?<br>Transport a vehicle? or to Complete a large-scale construction project?</div>

  <div class="abs card left">
    <div class="photo" role="img" aria-label="Photo of a black 30 foot equipment trailer with wooden deck"></div>
    <h2>Strider 30' X 7' 14K LBS</h2>
    <p>This Strider trailer is 30 feet long, by 7 feet wide. It features removable fenders, mini-mega ramps that can be folded flat to increase deck space. Massive front tool-box (we can fill it with whatever straps, chains, binder, etc... you need. We have car hauling strap kits, chains and binders, and everything in between).</p>
  </div>
  <div class="abs price left">
    <div class="col"><div class="title">Week Days</div><div class="days">Monday - Thursday</div><div class="rate">$100/Day*<span>$500/Week*</span></div></div>
    <div class="divider"></div>
    <div class="col"><div class="title">Weekends</div><div class="days">Friday - Sunday</div><div class="rate">$100/Day*<span>$250/Weekend*</span></div></div>
  </div>

  <svg class="abs connectors" width="432" height="120" viewBox="0 0 432 120" aria-hidden="true">
    <g fill="none" stroke="#EE7325" stroke-width="1.5" stroke-dasharray="6 5">
      <path d="M2 34 L54 10"/><path d="M382 10 L430 34"/>
      <path d="M2 114 L54 90"/><path d="M382 90 L430 114"/>
    </g>
  </svg>
  <div class="abs category">CAR/EQUIPMENT<br>TRAILERS</div>

  <svg class="abs arrow" style="left:413px" width="56" height="62" viewBox="0 0 56 62" aria-hidden="true">
    <path d="M2 31 L30 2 L30 18 L54 18 L54 44 L30 44 L30 60 Z" fill="#fff" stroke="#4a4a4c" stroke-width="2"/>
  </svg>
  <svg class="abs arrow" style="left:764px" width="56" height="62" viewBox="0 0 56 62" aria-hidden="true">
    <path d="M54 31 L26 2 L26 18 L2 18 L2 44 L26 44 L26 60 Z" fill="#fff" stroke="#4a4a4c" stroke-width="2"/>
  </svg>
  <div class="abs meet bebas">Meet Our<br><span class="hl">Superstars</span></div>

  <div class="abs map" role="img" aria-label="Map of East Michigan counties served, with a pin at the rental location"></div>
  <div class="abs serving bebas">Serving <span>East Michigan</span></div>
  <div class="abs counties">WAYNE. MI, MONROE. MI, GENESEE. MI,<br>ST. CLAIR. MI, LAPEER. MI, WASHTENAW. MI,<br>LENAWEE. MI, LIVINGSTON. MI</div>
  <div class="abs contact">Always contact us with any questions!</div>

  <div class="abs card right">
    <div class="photo" role="img" aria-label="Photo of a black 20 foot car hauler trailer in a parking lot"></div>
    <h2>QT 20' X 7' Car Hauler</h2>
    <p>Only 2 years old. Comes with a winch. Removable fenders if needed. All straps and tie downs provided. Has pull out ramps, we can also provide 7' aluminum ramp extensions that can give you a very gradual loading angle. Rear jacks keep it stable for loading. This is the cream of the crop of car haulers</p>
  </div>
  <div class="abs price right">
    <div class="col"><div class="title">Week Days</div><div class="days">Monday - Thursday</div><div class="rate">$85/Day*<span>$350/</span><small>Week*</small></div></div>
    <div class="divider"></div>
    <div class="col"><div class="title">Weekends</div><div class="days">Friday - Sunday</div><div class="rate">$85/Day*<span>$300/</span><small>Weekend*</small></div></div>
  </div>
</div>
</body>
</html>
```